One piece Trade show banner, 8' x 8' square

One piece banner for trade show
8' x 8' airborne geophysical company

Target Market(s)

Business

Industry/Entity Type

mineral exploration and science

Colors
0054AA
0677BA
7BADD7
CADEEF
E8F1F8
FFC000
F8CF3A
FAE287
FDF2CF
FEFAEE

Requirements
Must have
• Company logo (attached), slogan (Airborne Geophysics for Discovery). We are looking for a new banner, for a standard 8 x 8' square one-piece booth. I have attached some pictures, our logo, our old banner for reference, and two examples from unrelated companies from a tradeshow that we like. If its possible I'd like to change the color of the helicopter from green to dark grey. IE, keep the orange and white, just change green to dark grey. Looking for a simple, clean design with minimal text.
Nice to have
• I have attached examples of banners that we like (2xIMG), plus our old 3-piece banner r.
Should not have
• Green in the helicopter. Please change the color of the helicopter with green/orange/white to dark grey/orange/white. IE change the green to dark grey and leave the orange and white alone. I've attached lots of pictures but I don't expect them all to be used.

```html
<!DOCTYPE html>
<html lang="en">
<head>
<meta charset="utf-8">
<title>Meridian AeroScan – Airborne Geophysics for Discovery</title>
<link href="https://fonts.googleapis.com/css2?family=Anton&family=Questrial&display=swap" rel="stylesheet">
<style>
  :root {
    --backdrop: #121212;
    --paper: #ffffff;
    --gold: #fbc02d;
    --ink: #2b2b2b;
    --shadow: rgba(0,0,0,0.75);
  }
  html, body { margin: 0; padding: 0; overflow: hidden; background: var(--backdrop); width: 1200px; height: 1200px; }
  .banner { display: block; width: 1200px; height: 1200px; }
  .headline { font-family: "Anton", "Oswald", sans-serif; }
  .headline-white { fill: var(--paper); }
  .headline-gold { fill: var(--gold); }
  .brand-name { font-family: "Questrial", "Century Gothic", sans-serif; fill: var(--ink); }
</style>
</head>
<body>
<svg class="banner" viewBox="0 0 1932 1932" xmlns="http://www.w3.org/2000/svg">
  <defs>
    <linearGradient id="mountainGrad" x1="0.2" y1="0" x2="0.5" y2="1">
      <stop offset="0" stop-color="#c3d6e0"/>
      <stop offset="0.22" stop-color="#a9c2d0"/>
      <stop offset="0.36" stop-color="#6f93a6"/>
      <stop offset="0.5" stop-color="#3f6f7c"/>
      <stop offset="0.68" stop-color="#35634f"/>
      <stop offset="0.85" stop-color="#4d6e5c"/>
      <stop offset="1" stop-color="#6f7c72"/>
    </linearGradient>
    <linearGradient id="lakeGrad" x1="0" y1="0" x2="0" y2="1">
      <stop offset="0" stop-color="#8a6f62"/>
      <stop offset="0.2" stop-color="#9b8a7d"/>
      <stop offset="0.42" stop-color="#b3aba0"/>
      <stop offset="0.52" stop-color="#9a948a"/>
      <stop offset="0.56" stop-color="#4aa8c2"/>
      <stop offset="0.75" stop-color="#2a9bc9"/>
      <stop offset="1" stop-color="#1787c4"/>
    </linearGradient>
    <linearGradient id="valleyGrad" x1="0" y1="0" x2="0" y2="1">
      <stop offset="0" stop-color="#e6e9ec"/>
      <stop offset="0.25" stop-color="#d3dce4"/>
      <stop offset="0.4" stop-color="#8aa4c0"/>
      <stop offset="0.55" stop-color="#6e8fb0"/>
      <stop offset="0.7" stop-color="#a8cc8a"/>
      <stop offset="1" stop-color="#4f8a3e"/>
    </linearGradient>
    <clipPath id="innerClip"><rect x="200" y="200" width="1530" height="1530"/></clipPath>
    <clipPath id="goldArcClip"><rect x="200" y="200" width="505" height="1530"/></clipPath>
    <clipPath id="lakeClip">
      <circle cx="760" cy="1290" r="580"/>
      <rect x="200" y="1290" width="1172" height="440"/>
    </clipPath>
    <clipPath id="mountainClip">
      <rect x="736" y="200" width="994" height="480"/>
      <circle cx="1250" cy="680" r="530"/>
    </clipPath>
    <clipPath id="valleyClip"><circle cx="1400" cy="1245" r="285"/></clipPath>
    <filter id="textShadow" x="-5%" y="-20%" width="115%" height="150%">
      <feDropShadow dx="6" dy="8" stdDeviation="5" flood-color="#000" flood-opacity="0.75"/>
    </filter>
  </defs>

  <rect class="backdrop" width="1932" height="1932" fill="var(--backdrop)"/>

  <g class="panel" clip-path="url(#innerClip)">
    <rect x="200" y="200" width="1530" height="1530" fill="var(--paper)"/>

    <circle class="gold-arc" cx="760" cy="1290" r="635" fill="var(--gold)" clip-path="url(#goldArcClip)"/>

    <rect class="photo-lake" role="img" aria-label="White and orange survey helicopter with a sensor boom flying low over a turquoise mountain lake beside a rocky slope"
          x="200" y="700" width="1172" height="1030" fill="url(#lakeGrad)" clip-path="url(#lakeClip)"/>

    <circle class="photo-ring" cx="1250" cy="680" r="560" fill="var(--paper)"/>
    <rect class="photo-mountain" role="img" aria-label="White and orange survey helicopter with sensor boom flying through a forested mountain valley"
          x="736" y="200" width="994" height="1010" fill="url(#mountainGrad)" clip-path="url(#mountainClip)"/>

    <circle class="badge-gold" cx="1400" cy="1245" r="345" fill="var(--gold)"/>
    <circle class="badge-ring" cx="1400" cy="1245" r="305" fill="var(--paper)"/>
    <rect class="photo-valley" role="img" aria-label="Blue survey helicopter with gold stripe flying over green valleys with distant mountains"
          x="1115" y="960" width="570" height="570" fill="url(#valleyGrad)" clip-path="url(#valleyClip)"/>
  </g>

  <g class="brand">
    <text class="brand-name" x="262" y="472" font-size="118" textLength="416" lengthAdjust="spacingAndGlyphs">Meridian</text>
    <text class="brand-name" x="678" y="512" font-size="44" text-anchor="end">AeroScan</text>
  </g>

  <g class="headline" filter="url(#textShadow)">
    <text class="headline-white" x="862" y="430" font-size="224" textLength="762" lengthAdjust="spacingAndGlyphs">AIRBORNE</text>
    <text class="headline-gold" x="862" y="553" font-size="128" textLength="762" lengthAdjust="spacingAndGlyphs">GEOPHYSICS FOR</text>
    <text class="headline-white" x="862" y="728" font-size="195" textLength="745" lengthAdjust="spacingAndGlyphs">DISCOVERY</text>
  </g>
</svg>
</body>
</html>
```